Website for a service provided by a Canadian Immigration Company

Design and Code a website for a Canadian immigration company which provides service to clients all across the world. the website should be very Canadian centric and have 4-5 pages. Basic, classy modern. I have the logo s already designed. Please contact me and I can send you some more details. It's basically a service which is provided to clients who are below 17 and need a guardian in canada to sign their documents that they will be looked after them. It's called custodianship. You can google the term and you will understand what it means
Updates

didn't realize it was just a day

Target Market(s)

17-55

Industry/Entity Type

Immigration

Coding

Coded - Design and coding required

Number of Pages Required

5+ page

Font styles to use
Sans Serif

Colors
EE7325
F08F49
F5BC92
FAE3D3
FDF4ED
EB3D1F
EC4F4E
F09395
F8D3D4
FCEDEE

Requirements
Must have
• Pages with some graphics, some small animations like clients served, projects completed

```html
<!DOCTYPE html>
<html lang="en">
<head>
<meta charset="utf-8">
<title>GuardianNorth – Custodianship Services in Canada</title>
<link href="https://fonts.googleapis.com/css2?family=Roboto:wght@400;500;700&display=swap" rel="stylesheet">
<style>
:root{
  --orange:#ee7325;
  --orange-mid:#f08f49;
  --peach:#f5bc92;
  --peach-light:#fae3d3;
  --red:#eb3d1f;
  --red-soft:#ec4f4e;
  --pink:#f8d3d4;
  --pink-light:#fcedee;
  --brand-red:#e2262f;
  --ink:#222226;
  --text:#55575c;
  --grey-bg:#eeeff1;
  --footer:#262628;
  --white:#ffffff;
}
*{box-sizing:border-box;margin:0;padding:0}
html,body{width:1200px;height:3655px;overflow:hidden}
body{position:relative;font-family:"Roboto",sans-serif;color:var(--ink);background:var(--white)}
.abs{position:absolute}

/* header */
.topline{left:0;top:0;width:1200px;height:4px;background:var(--orange)}
.header{left:0;top:4px;width:1200px;height:105px;background:var(--white)}
.brand{display:flex;align-items:center;gap:12px;font-weight:500;font-size:31px;color:var(--ink);letter-spacing:-.3px}
.brand-dot{width:34px;height:34px;border-radius:50%;background:var(--brand-red)}
.header .brand{position:absolute;left:111px;top:30px}
.nav{position:absolute;top:74px;display:flex;font-size:15px;font-weight:500;color:var(--ink)}
.nav a{position:absolute;white-space:nowrap;color:inherit;text-decoration:none;transform:translateX(-50%)}
.nav .active{color:var(--orange)}
.nav-home-icon{left:618px;top:52px}

/* buttons */
.btn{display:flex;height:46px}
.btn-label{display:flex;align-items:center;padding:0 24px 0 28px;background:var(--brand-red);color:var(--white);font-weight:700;font-size:15px;clip-path:polygon(10px 0,100% 0,100% 100%,0 100%);white-space:nowrap}
.btn-tail{width:62px;background:var(--white);display:flex;align-items:center;justify-content:center;box-shadow:2px 2px 6px rgba(0,0,0,.08)}
.btn.light .btn-label{background:var(--white);color:var(--brand-red)}
.btn.small{height:40px}
.btn.small .btn-label{font-size:14px;padding:0 18px 0 22px}
.btn.small .btn-tail{width:52px}

/* hero */
.hero{left:0;top:109px;width:1200px;height:640px;background:linear-gradient(90deg,#f6f6f6 0%,#eceeee 45%,#e3e4e2 100%);clip-path:polygon(0 0,100% 0,100% 515px,50% 625px,0 515px)}
.hero-leaf{left:530px;top:0;width:520px;height:520px;background:radial-gradient(circle,rgba(245,188,146,.8) 0%,rgba(245,188,146,0) 70%)}
.hero-photo{left:600px;top:0;width:600px;height:640px;background:linear-gradient(160deg,#d8c9bd 0%,#b99784 35%,#5a6e8a 70%,#e8e6e2 100%);-webkit-mask:linear-gradient(90deg,transparent 0,#000 90px);mask:linear-gradient(90deg,transparent 0,#000 90px)}
.hero-band{left:0;top:600px;width:1200px;height:150px;background:var(--orange);clip-path:polygon(150px 45px,599px 142px,1200px 22px,1200px 30px,599px 125px)}
.hero-copy{left:111px;top:230px}
.hero-copy .eyebrow{font-size:35px;font-weight:500;color:var(--ink)}
.hero-copy h1{font-size:60px;font-weight:700;color:var(--brand-red);line-height:1.1;margin-top:2px}
.hero-copy p{font-size:18.5px;line-height:27px;width:440px;color:var(--ink);margin-top:18px}
.hero-copy .btn{margin-top:28px}
.slider-dots{left:111px;top:587px;display:flex;gap:10px}
.slider-dots span{height:4px;width:24px;background:var(--red)}
.slider-dots span:first-child{width:68px;background:var(--orange)}

/* about */
.about-back{left:77px;top:879px;width:434px;height:440px;background:var(--pink-light);clip-path:polygon(14px 0,100% 0,100% 100%,0 100%)}
.about-frame{left:113px;top:840px;width:462px;height:440px;background:var(--white);box-shadow:0 6px 18px rgba(0,0,0,.18);padding:8px;transform:skewX(-2deg)}
.about-photo{width:100%;height:100%;background:linear-gradient(135deg,#c9c6c2 0%,#8f8a86 40%,#6b5f58 70%,#d4d2cf 100%)}
.section-title{font-size:43px;font-weight:700;color:var(--ink);letter-spacing:.2px}
.section-title em{font-style:normal;color:var(--brand-red)}
.about-text{left:634px;top:870px;width:440px}
.about-text p{font-size:13px;line-height:25.5px;color:var(--text);margin-top:22px}
.about-text p:first-of-type{margin-top:24px}
.about-text .btn{margin-top:38px}

/* lower background */
.lower-bg{left:0;top:2140px;width:1200px;height:1300px;background:linear-gradient(160deg,#f4f4f5 0%,#e9eaec 50%,#f1f1f2 100%)}

/* services */
.services{left:0;top:1414px;width:1200px;height:941px;background:linear-gradient(160deg,#ef8a45 0%,#e9541f 40%,#e73a2c 75%,#eb4a45 100%);clip-path:polygon(0 125px,1001px 0,1200px 125px,1200px 813px,227px 941px,0 813px)}
.services-title{left:0;top:1555px;width:1200px;text-align:center;color:var(--white);font-size:43px;font-weight:700}
.services-lead{left:170px;top:1625px;width:860px;text-align:center;color:var(--white);font-size:17px;line-height:29px}
.card{top:1725px;width:308px;height:404px;background:linear-gradient(150deg,#ddd9d4 0%,#a99c90 45%,#53657d 100%)}
.card-caption{position:absolute;left:20px;right:20px;bottom:18px;height:74px;background:var(--white);text-align:center;padding-top:12px}
.card-caption h3{font-size:16.5px;font-weight:500;color:var(--ink)}
.card-caption a{display:inline-block;margin-top:6px;font-size:12.5px;font-weight:500;color:var(--brand-red);text-decoration:underline}
.services-btn{left:495px;top:2186px}

/* contact */
.contact-title{left:0;top:2420px;width:1200px;text-align:center}
.info{top:2530px;width:260px;text-align:center;font-size:13.5px;line-height:21px;color:var(--text)}
.info svg{display:block;margin:0 auto 10px}
.info strong{display:block;color:var(--ink);font-weight:500;font-size:14px}
.field{background:var(--white);border:1px solid #e4e4e6;box-shadow:0 2px 6px rgba(0,0,0,.05);font-size:13px;color:#67696d;padding:0 22px;display:flex;align-items:center}
.field.area{align-items:flex-start;padding-top:18px}
.submit{left:505px;top:3068px}
.submit .btn-label{padding:0 22px 0 28px}
.chat-bubble{left:970px;top:3225px;width:74px;height:74px;border-radius:50%;background:#3fc04f;box-shadow:0 4px 10px rgba(0,0,0,.2)}

/* footer */
.footer{left:0;top:3240px;width:1200px;height:415px;background:var(--footer);clip-path:polygon(0 147px,900px 147px,1200px 0,1200px 100%,0 100%)}
.footer .brand{position:absolute;left:0;right:0;top:180px;justify-content:center;color:var(--white);font-size:34px;font-weight:500}
.footer .brand-dot{background:var(--white);width:40px;height:40px}
.footer-nav{position:absolute;top:282px;left:0;width:1200px;height:20px;color:var(--white);font-size:14.5px;font-weight:700}
.footer-nav span{position:absolute;transform:translateX(-50%);white-space:nowrap}
.copyright{position:absolute;top:338px;left:0;width:1200px;text-align:center;color:var(--white);font-size:11px}
</style>
</head>
<body>

<div class="abs topline"></div>
<header class="abs header">
  <div class="brand"><span class="brand-dot"></span>guardiannorth.ca</div>
  <a class="abs btn small" style="left:930px;top:19px;text-decoration:none">
    <span class="btn-label">Get Started</span>
    <span class="btn-tail"><svg width="20" height="14" viewBox="0 0 20 14"><path d="M1 7h16M12 2l5 5-5 5" stroke="#e2262f" stroke-width="2.2" fill="none"/></svg></span>
  </a>
  <svg class="abs" style="left:606px;top:49px" width="24" height="18" viewBox="0 0 24 18"><path d="M12 2 2 7l10 5 10-5z M6 9v5c3 3 9 3 12 0V9" stroke="#ee7325" stroke-width="2" fill="none"/></svg>
  <nav class="nav" style="left:0;top:74px">
    <a class="active" style="left:618px">Home</a>
    <a style="left:713px">About Us</a>
    <a style="left:831px">Our Services</a>
    <a style="left:962px">Testimonials</a>
    <a style="left:1068px">Blogs</a>
  </nav>
</header>

<section>
  <div class="abs hero">
    <div class="abs hero-leaf"></div>
    <div class="abs hero-photo" role="img" aria-label="Smiling family of three embracing at home"></div>
  </div>
  <div class="abs hero-band"></div>
  <div class="abs hero-copy">
    <div class="eyebrow">Welcome To</div>
    <h1>GuardianNorth</h1>
    <p>The standard chunk of Lorem Ipsum used since the 1500s is reproduced below for those interested. Sections 1.10.32 and</p>
    <div class="btn">
      <span class="btn-label">Get Started</span>
      <span class="btn-tail"><svg width="22" height="16" viewBox="0 0 22 16"><path d="M1 8h18M14 2l6 6-6 6" stroke="#e2262f" stroke-width="2.4" fill="none"/></svg></span>
    </div>
  </div>
  <div class="abs slider-dots"><span></span><span></span><span></span></div>
</section>

<section>
  <div class="abs about-back"></div>
  <div class="abs about-frame"><div class="about-photo" role="img" aria-label="Parent hugging a young girl"></div></div>
  <div class="abs about-text">
    <h2 class="section-title">ABOUT <em>US</em></h2>
    <p>There are many variations of passages of Lorem Ipsum available, but the majority have suffered alteration in some form, by injected humour, or randomised words which don't look even slightly believable. If you are going to use a passage of Lorem Ipsum, you need to be sure there isn't anything embarrassing hidden in the middle of text.</p>
    <p>It uses a dictionary of over 200 Latin words, combined with a handful of model sentence structures, to generate Lorem Ipsum which looks reasonable. The generated Lorem Ipsum is therefore always free from repetition, injected humour, or non-characteristic words etc.</p>
    <div class="btn">
      <span class="btn-label">Read More</span>
      <span class="btn-tail"><svg width="22" height="16" viewBox="0 0 22 16"><path d="M1 8h18M14 2l6 6-6 6" stroke="#e2262f" stroke-width="2.4" fill="none"/></svg></span>
    </div>
  </div>
</section>

<div class="abs lower-bg"></div>

<section>
  <div class="abs services"></div>
  <h2 class="abs services-title">OUR SERVICES</h2>
  <p class="abs services-lead">The standard chunk of Lorem Ipsum used since the 1500s is reproduced below for those interested. Sections 1.10.32 and 1.10.33 from "de Finibus Bonorum et Malorum" by Cicero are also</p>
  <div class="abs card" style="left:111px" role="img" aria-label="Father and daughter giving a high five">
    <div class="card-caption"><h3>Lorem Ipsum Is A Dummy</h3><a>View Details</a></div>
  </div>
  <div class="abs card" style="left:446px" role="img" aria-label="Mother helping a schoolgirl with her backpack">
    <div class="card-caption"><h3>Lorem Ipsum Is A Dummy</h3><a>View Details</a></div>
  </div>
  <div class="abs card" style="left:780px" role="img" aria-label="Tutor helping children with homework">
    <div class="card-caption"><h3>Lorem Ipsum Is A Dummy</h3><a>View Details</a></div>
  </div>
  <div class="abs btn services-btn light">
    <span class="btn-label">View Services</span>
    <span class="btn-tail"><svg width="22" height="16" viewBox="0 0 22 16"><path d="M1 8h18M14 2l6 6-6 6" stroke="#e2262f" stroke-width="2.4" fill="none"/></svg></span>
  </div>
</section>

<section>
  <h2 class="abs section-title contact-title">GET IN TOUCH <em>WITH US</em></h2>
  <div class="abs info" style="left:185px">
    <svg width="34" height="34" viewBox="0 0 24 24"><path d="M6.6 10.8a15 15 0 0 0 6.6 6.6l2.2-2.2a1 1 0 0 1 1-.25 11.4 11.4 0 0 0 3.6.6 1 1 0 0 1 1 1V20a1 1 0 0 1-1 1A17 17 0 0 1 3 4a1 1 0 0 1 1-1h3.5a1 1 0 0 1 1 1c0 1.25.2 2.45.6 3.6a1 1 0 0 1-.25 1z" fill="#e9541f"/></svg>
    <strong>Contact Number:</strong>+1 555 0142-776
  </div>
  <div class="abs info" style="left:461px;width:260px">
    <svg width="34" height="40" viewBox="0 0 24 28"><path d="M12 1a9 9 0 0 0-9 9c0 7 9 17 9 17s9-10 9-17a9 9 0 0 0-9-9z" fill="#e9541f"/><circle cx="12" cy="10" r="4.5" fill="#fff"/></svg>
    24B, GuardianNorth, The standard chunk of Lorem Ipsum used, Canada.
  </div>
  <div class="abs info" style="left:737px">
    <svg width="34" height="34" viewBox="0 0 24 24"><rect x="2" y="5" width="20" height="14" fill="#e9541f"/><path d="M2 5l10 8 10-8" stroke="#fff" stroke-width="1.6" fill="none"/></svg>
    <strong>Email Address:</strong>hello@guardiannorth.ca
  </div>

  <form>
    <div class="abs field" style="left:153px;top:2745px;width:429px;height:40px">First Name</div>
    <div class="abs field" style="left:616px;top:2745px;width:429px;height:40px">Last Name</div>
    <div class="abs field" style="left:153px;top:2808px;width:429px;height:40px">Email Address</div>
    <div class="abs field" style="left:616px;top:2808px;width:429px;height:40px">Contact Number</div>
    <div class="abs field area" style="left:153px;top:2872px;width:892px;height:220px">Your Message Goes Here....</div>
    <div class="abs btn submit">
      <span class="btn-label">Submit Now</span>
      <span class="btn-tail"><svg width="22" height="16" viewBox="0 0 22 16"><path d="M1 8h18M14 2l6 6-6 6" stroke="#e2262f" stroke-width="2.4" fill="none"/></svg></span>
    </div>
  </form>
</section>

<footer class="abs footer">
  <div class="brand"><span class="brand-dot"></span>guardiannorth.ca</div>
  <div class="footer-nav">
    <span style="left:226px">HOME</span>
    <span style="left:303px">|</span>
    <span style="left:396px">ABOUT US</span>
    <span style="left:488px">|</span>
    <span style="left:580px">SERVICES</span>
    <span style="left:670px">|</span>
    <span style="left:759px">REVIEWS</span>
    <span style="left:847px">|</span>
    <span style="left:949px">CONTACT US</span>
  </div>
  <div class="copyright">Copyright © 2023 GuardianNorth | All Rights Reserved.</div>
</footer>
<div class="abs chat-bubble" role="img" aria-label="Chat button"></div>

</body>
</html>
```